International Career Development Workshop

I need a Powerpoint revised and designed in a more professional manner for a presentation I will be giving. We are an International Education Company that provides students with Internships Abroad, and are expanding our career development programming to offer more guidance through on-site workshops. I am happy to send along our website to showcase the colors and fonts we use, but we tend to use royal blue, lime green, and white in our color scheme. The final design should communicate opportunity and self-awareness within college students.

Target Market(s)

College Students, University Partners, and International Education Community

Industry/Entity Type

Education

Font styles to use
Sans Serif

Colors
9bcb3b
0355a3
ffffff

Requirements
Must have
• Our logo, our color scheme, a unified, professional theme throughout, Watermark of our logo, thematic sections spread across four sections.
Nice to have
• Videos and graphics
Should not have
• Spelling Errors, sloppy design

```html
<!DOCTYPE html>
<html lang="en">
<head>
<meta charset="UTF-8">
<title>Project Title Here</title>
<link rel="stylesheet" href="https://fonts.googleapis.com/css2?family=Lato:wght@400;700;900&family=Lora:wght@400;700&display=swap">
<style>
  :root {
    --royal-blue: #0355a3;
    --lime: #9bcb3b;
    --white: #ffffff;
    --body-grey: #555555;
    --subtitle-blue: #1d5b9e;
    --marker-blue: #3f74b3;
  }
  * { margin: 0; padding: 0; box-sizing: border-box; }
  html, body {
    width: 1200px;
    height: 900px;
    overflow: hidden;
    background: var(--white);
  }
  .slide {
    position: relative;
    width: 1200px;
    height: 900px;
    background: var(--white);
    overflow: hidden;
  }
  .slide-header {
    position: absolute;
    top: 0; left: 0;
    width: 1200px;
    height: 85px;
    background: var(--royal-blue);
    display: flex;
    align-items: center;
    justify-content: space-between;
    padding: 0 22px 0 33px;
  }
  .slide-title {
    font-family: "Lato", sans-serif;
    font-weight: 900;
    font-size: 39px;
    color: var(--white);
    letter-spacing: 0.2px;
  }
  .brand {
    display: flex;
    align-items: center;
    gap: 14px;
  }
  .brand-mark {
    width: 46px;
    height: 46px;
    border-radius: 50%;
    background: var(--white);
  }
  .brand-name {
    font-family: "Lato", sans-serif;
    font-weight: 700;
    font-size: 22px;
    line-height: 1.05;
    color: var(--white);
    letter-spacing: 0.5px;
  }
  .sections {
    position: absolute;
    left: 28px;
    top: 148px;
    width: 1100px;
  }
  .section {
    margin-bottom: 53px;
  }
  .section:nth-child(2) { margin-bottom: 71px; }
  .section-heading {
    display: flex;
    align-items: center;
    gap: 14px;
    margin-bottom: 4px;
  }
  .section-marker {
    width: 30px;
    height: 30px;
    border-radius: 50%;
    background: var(--marker-blue);
    margin-left: 14px;
  }
  .section-subtitle {
    font-family: "Lora", serif;
    font-weight: 700;
    font-size: 31px;
    color: var(--subtitle-blue);
  }
  .section-body {
    margin-left: 72px;
    font-family: "Lora", serif;
    font-weight: 400;
    font-size: 22.5px;
    line-height: 39px;
    color: var(--body-grey);
    text-indent: 7px;
  }
  .slide-footer {
    position: absolute;
    left: 0; bottom: 0;
    width: 1200px;
    height: 41px;
    background: var(--lime);
    display: flex;
    align-items: center;
    padding-left: 30px;
  }
  .copyright {
    font-family: "Lato", sans-serif;
    font-size: 22px;
    color: var(--white);
  }
</style>
</head>
<body>
<div class="slide">
  <header class="slide-header">
    <h1 class="slide-title">PROJECT TITLE HERE</h1>
    <div class="brand">
      <span class="brand-mark"></span>
      <span class="brand-name">WORLDWARD<br>PROGRAMS</span>
    </div>
  </header>

  <main class="sections">
    <section class="section">
      <div class="section-heading">
        <span class="section-marker"></span>
        <h2 class="section-subtitle">Subtitle Here</h2>
      </div>
      <p class="section-body">chocolate chocolate cake carrot cake dragée candy canes gummies bear cake icing oat cake jelly chocolate chocolate cake carrot cake dragée candy canes gummies bear Gummies cake icing oat cake jelly chocolate chocolate cake carrot cake dragée candy canes</p>
    </section>
    <section class="section">
      <div class="section-heading">
        <span class="section-marker"></span>
        <h2 class="section-subtitle">Subtitle Here</h2>
      </div>
      <p class="section-body">chocolate chocolate cake carrot cake dragée candy canes gummies bear cake icing oat cake jelly chocolate chocolate cake carrot cake dragée candy canes gummies bear Gummies cake icing oat cake jelly chocolate chocolate cake carrot cake dragée candy canes</p>
    </section>
    <section class="section">
      <div class="section-heading">
        <span class="section-marker"></span>
        <h2 class="section-subtitle">Subtitle Here</h2>
      </div>
      <p class="section-body">chocolate chocolate cake carrot cake dragée candy canes gummies bear cake icing oat cake jelly chocolate chocolate cake carrot cake dragée candy canes gummies bear Gummies cake icing oat cake jelly chocolate chocolate cake carrot cake dragée candy canes</p>
    </section>
  </main>

  <footer class="slide-footer">
    <p class="copyright">Copyright text here</p>
  </footer>
</div>
</body>
</html>
```